Business Card Design

We like to use greens as you will see in our logo (but not TOO much green). We are a Dental Clinic in a somewhat eccentric community. We do not like the dated sharp designs which we see many dentists use. We're looking for something bright and fresh while still maintaining the integrity of the profession. Elegance is not necessarily what we are going for... we need for the design to be "mature" but also up-lifting.

See our logo.
Updates

Project Deadline Extended
Reason: We have 5 designs which we like. But we'd like to see a few more before committing to a design.

Project Deadline Extended
Reason: We are awaiting revisions to this project. We are still welcoming designs while we wait to see if designers are able to provide to us the revisions we require in order to proceed with a selection.

Target Market(s)

Younger families - ages late 20's to early 40's

Industry/Entity Type

Business

Contact Information for Business Card

Corwel T. Banfry DDS 2730 W. Halvert Rd. Ste. 7 Royal Oak, MI 48391 (248)555-0174 FX (248)555-0189 info@BrightwellDentalCareMi.com BrigthwellDentalCareMi.com on the back of the card we need an appointment reminder (For____ Date___ Time____) with "If you are unable to keep your appointment, kindly give 48 hours notice" at the bottom. No use of teeth in the design. DOUBLE SIDED DESIGN

Requirements
Should not have
• The use of pictures of teeth

```html
<!DOCTYPE html>
<html lang="en">
<head>
<meta charset="utf-8">
<title>Brightwell Dental Care – Business Card</title>
<link rel="stylesheet" href="https://fonts.googleapis.com/css2?family=Arimo:wght@400;700&family=Cinzel:wght@600&family=Open+Sans:ital,wght@0,400;0,700;1,600&display=swap">
<style>
  :root {
    --green-dark: #1f6b3a;
    --green-mid: #3aa655;
    --green-light: #8cc63f;
    --ink: #2b2b2b;
    --card: #ffffff;
    --backdrop: #e9ece8;
    --box-line: #3a3a3a;
  }
  * { box-sizing: border-box; margin: 0; padding: 0; }
  html, body { width: 1200px; height: 1162px; overflow: hidden; }
  body { background: var(--backdrop); position: relative; font-family: "Arimo", Arial, sans-serif; color: var(--ink); }

  .card { position: absolute; width: 910px; background: var(--card); overflow: hidden; box-shadow: 0 4px 14px rgba(0,0,0,.15); }
  .card--front { left: 35px; top: 21px; height: 520px; border-radius: 44px; }
  .card--back { left: 243px; top: 582px; height: 518px; border-radius: 18px; border: 1.5px solid #555; }

  /* brand name */
  .brand { position: absolute; color: var(--green-dark); font-family: "Open Sans", sans-serif; font-weight: 700; line-height: 1; }
  .brand__name { display: block; }
  .brand__sub { display: block; letter-spacing: .06em; }
  .card--front .brand { left: 62px; top: 92px; }
  .card--front .brand__name { font-size: 72px; }
  .card--front .brand__sub { font-size: 34px; margin-top: 10px; }
  .card--back .brand { right: 52px; top: 58px; text-align: right; }
  .card--back .brand__name { font-size: 46px; }
  .card--back .brand__sub { font-size: 22px; margin-top: 6px; }
  .brand__rule { display: block; height: 3px; background: var(--green-light); margin-top: 8px; }

  .address { position: absolute; left: 554px; top: 82px; font-size: 23px; line-height: 1.45; }

  .dentist { position: absolute; left: 60px; top: 290px; color: var(--green-dark); font-weight: 700; font-size: 34px; }
  .dentist__title { font-size: 22px; color: #333; }

  .contact { position: absolute; left: 58px; top: 350px; list-style: none; font-size: 23px; }
  .contact li { display: flex; align-items: center; gap: 8px; height: 42px; }
  .contact li:last-child { font-size: 21px; }
  .contact svg { width: 20px; height: 20px; flex: none; }

  .corner { position: absolute; left: 0; top: 0; width: 910px; height: 520px; }

  /* back */
  .appointment__title { position: absolute; left: 70px; top: 96px; font-family: "Cinzel", serif; font-weight: 600; font-size: 32px; color: var(--green-dark); letter-spacing: .02em; }
  .field { position: absolute; font-size: 24px; display: flex; align-items: baseline; }
  .field__line { border-bottom: 2px dotted #666; height: 1px; display: inline-block; margin: 0 8px; }
  .field--name { left: 79px; top: 180px; }
  .field--name .field__line { width: 660px; margin-left: 18px; }
  .field--date { left: 79px; top: 244px; }
  .field--date .field__line.date { width: 225px; margin-left: 36px; }
  .field--date .field__line.time { width: 240px; }
  .field--next { left: 79px; top: 308px; }
  .next-boxes { position: absolute; left: 328px; top: 304px; display: flex; gap: 14px; }
  .next-boxes span { width: 163px; height: 36px; border: 2px solid var(--box-line); border-radius: 5px; }

  .weekdays { position: absolute; left: 0; top: 360px; width: 100%; height: 74px; display: flex; }
  .weekdays__main { background: var(--green-dark); width: 745px; flex: none; display: flex; align-items: center; padding-left: 76px; gap: 16px; }
  .weekdays__sat { background: var(--green-mid); flex: 1; margin-left: 4px; display: flex; align-items: center; padding-left: 24px; }
  .day { color: #fff; font-family: "Open Sans", sans-serif; font-weight: 700; font-size: 24px; display: flex; align-items: center; gap: 10px; white-space: nowrap; }
  .day__box { width: 54px; height: 34px; background: #fff; border-radius: 5px; flex: none; }

  .notice { position: absolute; left: 0; width: 100%; top: 456px; text-align: center; font-family: "Open Sans", sans-serif; font-style: italic; font-weight: 600; font-size: 23px; color: #222; }
</style>
</head>
<body>

<section class="card card--front" aria-label="Business card front">
  <svg class="corner" viewBox="0 0 910 520" aria-hidden="true">
    <polygon points="612,520 910,259 910,520" fill="var(--green-dark)"/>
    <line x1="589" y1="524" x2="912" y2="240" stroke="var(--green-light)" stroke-width="7"/>
  </svg>

  <div class="brand">
    <span class="brand__name">Brightwell</span>
    <span class="brand__sub">DENTAL CARE</span>
    <span class="brand__rule"></span>
  </div>

  <p class="address">2730 W. Halvert Rd.<br>Ste. 7 Royal Oak, MI 48391</p>

  <h1 class="dentist">Corwel T. Banfry, <span class="dentist__title">DDS</span></h1>

  <ul class="contact">
    <li>
      <svg viewBox="0 0 20 20"><circle cx="10" cy="10" r="8.5" fill="none" stroke="#333" stroke-width="1.5"/><path d="M7 5.5c-1 1-1 3 1 5.5s4 3.5 5 2.5l.8-.8-1.8-1.6-1 .8c-.8-.4-2-1.6-2.4-2.4l.8-1-1.6-1.8z" fill="#333"/></svg>
      (248) 555-0174
    </li>
    <li>
      <svg viewBox="0 0 20 20"><rect x="5" y="3" width="10" height="6" fill="#333"/><rect x="2" y="8" width="16" height="8" rx="2" fill="#333"/><circle cx="5.5" cy="16.5" r="1.8" fill="#333"/><circle cx="14.5" cy="16.5" r="1.8" fill="#333"/></svg>
      (248) 555-0189
    </li>
    <li>
      <svg viewBox="0 0 20 20"><rect x="2" y="6" width="16" height="10" fill="#333"/><path d="M2 6l8 6 8-6" fill="none" stroke="#fff" stroke-width="1.4"/><path d="M4 6l6-3 6 3" fill="#333"/></svg>
      info@BrightwellDentalCareMi.com
    </li>
    <li>
      <svg viewBox="0 0 20 20" fill="none" stroke="#333" stroke-width="1.4"><circle cx="10" cy="10" r="8"/><ellipse cx="10" cy="10" rx="3.5" ry="8"/><line x1="2" y1="10" x2="18" y2="10"/><line x1="3.5" y1="6" x2="16.5" y2="6"/><line x1="3.5" y1="14" x2="16.5" y2="14"/></svg>
      BrigthwellDentalCareMi.com
    </li>
  </ul>
</section>

<section class="card card--back" aria-label="Appointment card back">
  <div class="brand">
    <span class="brand__name">Brightwell</span>
    <span class="brand__sub">DENTAL CARE</span>
    <span class="brand__rule"></span>
  </div>

  <h2 class="appointment__title">YOUR APPOINTMENT</h2>

  <div class="field field--name">Name :<span class="field__line"></span></div>
  <div class="field field--date">Date :<span class="field__line date"></span>Time :<span class="field__line time"></span>am / pm</div>
  <div class="field field--next">Next Appointment</div>
  <div class="next-boxes"><span></span><span></span><span></span></div>

  <div class="weekdays">
    <div class="weekdays__main">
      <span class="day">MON <span class="day__box"></span></span>
      <span class="day">TUE <span class="day__box"></span></span>
      <span class="day">WED <span class="day__box"></span></span>
      <span class="day">THU <span class="day__box"></span></span>
      <span class="day">FRI <span class="day__box"></span></span>
    </div>
    <div class="weekdays__sat">
      <span class="day">SAT <span class="day__box"></span></span>
    </div>
  </div>

  <p class="notice">If you are unable to keep your appointment, kindly give 48 hours notice</p>
</section>

</body>
</html>
```